Chamber of Commerce Web Design Project

We are working with Harborlight Chamber of Commerce. They are a new chamber of commerce forming in SoCal.
Some sites to use for inspiration:
https://brevinmarchamber.org
https://quellford.org
https://www.dorwickhavenchamber.com
https://www.tpchamber.com
https://velmorintcc.org
Thank you for taking the time to consider designing a website for us. We are web developers based in Stockton, CA, USA. Most of our projects go through the same process. Understanding this process may help you win a project with us. We custom-code all of our websites in-house. We don’t have any requirements as to what tools you use for your design, but we prefer Figma files. For any design that we label as four-stars, we send it to the client for review. The client picks the final design they want us to use. Once we complete this process, we will continue to show additional clients all the four-star sites and purchase them later. Your designs will have multiple chances to sell. For better chances of success, we ask that you follow these guidelines.
IMAGES:
If you use any images or icons in the design, we ask that you have a link to the asset so we can purchase the image/icon. Most of the designs we submit do not have the customer’s images on them unless they have some great images. Be creative; show us the feeling you are trying to portray with your image choices. Use any royalty-free site you choose. We subscribe to Adobe and mainly use their images, but we can purchase images outside of Adobe.
PLEASE NOTE: we will not submit designs to clients with watermarks on the images.
FONTS:
We ask that you identify the fonts used in the design. This can be done in a message if you want. We typically use Google Fonts and Adobe Fonts.
CONTENT:
We're always open to different content and ideas. We often submit designs with stock images so the client can see our vision. We typically take pictures after the website launch to use their images with our vision. Lorem Ipsum is fine for paragraphs, but we ask that you write the headers in correct English. We want to be able to show the vision and identify the sections of the website.
INSPIRATION:
We typically add a couple of links in the brief of websites we like to help you get started in your design.
REVISIONS:
We do not often ask for revisions of the designs unless we see something in the design that may not appeal to the client. If there are slight changes that we want to make, we do that in the development process.
FEEDBACK:
We rarely give feedback on designs during the design process. We are working on many website projects and do not have the time to provide feedback. We usually respond if your request is well thought out and asks specific questions, but a note asking “feedback, please” usually goes unanswered.

```html
<!DOCTYPE html>
<html lang="en">
<head>
<meta charset="utf-8">
<title>Harborlight Chamber of Commerce</title>
<link href="https://fonts.googleapis.com/css2?family=Archivo:wght@400;500;600;700;800&family=Lato:wght@400;700&display=swap" rel="stylesheet">
<style>
:root{
  --blue:#1a66f5;
  --blue-soft:#dde8fb;
  --yellow:#fec41a;
  --ink:#121212;
  --grey:#555b66;
  --white:#ffffff;
  --footer-bg:#fbf1ef;
  --head:"Archivo",Arial,sans-serif;
  --body:"Lato",Arial,sans-serif;
}
*{box-sizing:border-box;margin:0;padding:0}
html,body{width:1200px;height:4320px;overflow:hidden;background:var(--white);color:var(--ink);font-family:var(--head)}
section,header,footer{position:relative;width:1200px;overflow:hidden}
.btn{position:absolute;display:flex;align-items:center;justify-content:center;background:var(--yellow);color:var(--ink);font:600 15px var(--head);border-radius:4px;text-decoration:none;z-index:2}
.accent{color:var(--blue);font-weight:700}
.photo{position:absolute}

/* header */
.site-header{height:87px;background:var(--white)}
.brand{position:absolute;left:109px;top:14px;display:flex;align-items:center;gap:10px}
.brand-mark{width:56px;height:56px;border-radius:50%;background:var(--blue)}
.brand-name{font:800 30px/0.95 var(--head);color:var(--blue);letter-spacing:.5px}
.brand-name small{display:block;font:800 13px var(--head);letter-spacing:.6px;margin-top:3px}
.nav a{position:absolute;top:37px;font:400 13px var(--head);color:var(--ink);text-decoration:none}
.nav a.current{top:31px;left:456px;width:70px;height:29px;line-height:29px;text-align:center;background:var(--blue);color:#fff;border-radius:3px}
.site-header .btn{left:975px;top:20px;width:111px;height:44px}

/* hero */
.hero{height:590px}
.hero-photo{inset:0;background:linear-gradient(180deg,#b7c3cb 0%,#9aa6ab 25%,#6f7a6a 45%,#4e5b3c 60%,#5c6b7d 72%,#3d4a2c 88%,#2f3a22 100%)}
.hero-shade{position:absolute;inset:0;background:rgba(0,0,0,.12)}
.hero h1{position:absolute;left:0;width:1200px;top:236px;text-align:center;color:#fff;font:700 60px/74px var(--head)}
.hero .btn{left:544px;top:409px;width:113px;height:40px}

/* services */
.services{height:790px}
.services-title{position:absolute;top:78px;left:0;width:1200px;text-align:center}
.section-title{font:400 44px var(--head);color:var(--ink)}
.lede{font:400 13px/24px var(--body);color:var(--grey)}
.services .lede{position:absolute;top:144px;left:220px;width:760px;text-align:center}
.service-card{position:absolute;top:231px;height:396px;border-radius:6px;overflow:hidden}
.service-card .photo{inset:0}
.service-card p{position:absolute;left:24px;bottom:20px;color:#fff;font:700 19px/27px var(--body)}
.service-card.featured{background:var(--blue)}
.service-card.featured p{left:0;right:0;text-align:center;bottom:50px}
.ring{position:absolute;left:39px;top:27px;width:240px;height:240px;border-radius:50%;border:5px solid #fff;background:linear-gradient(160deg,#d6cfc5,#8c7c6c)}
.services .btn{left:545px;top:660px;width:110px;height:42px}

/* impact */
.impact{height:757px}
.impact-photo{left:0;top:0;width:1200px;height:413px;background:linear-gradient(90deg,#eef1ec 0%,#dfe3dc 25%,#a49c92 45%,#5e5a57 65%,#8a8782 85%,#d2d0cc 100%)}
.impact .section-title{position:absolute;left:112px;top:60px}
.stat{position:absolute;left:112px;width:444px;height:138px;background:var(--blue-soft);border-radius:5px}
.stat svg{position:absolute;left:36px;top:44px}
.stat strong{position:absolute;left:128px;top:24px;font:600 40px var(--head)}
.stat span{position:absolute;left:128px;top:78px;font:400 24px var(--head)}
.impact-pitch{position:absolute;left:643px;top:440px;width:490px;color:var(--blue);font:600 28px/43px var(--head)}
.impact-copy{position:absolute;left:647px;top:587px;width:460px;font:400 13px/26px var(--body);color:var(--grey)}

/* investors */
.investors{height:213px;background:var(--blue)}
.investors h2{position:absolute;top:38px;width:1200px;text-align:center;color:#fff;font:700 44px var(--head)}
.investor{position:absolute;top:141px;display:flex;align-items:center;gap:6px;color:#fff;font:700 15px var(--head)}
.investor i{display:block;width:16px;height:16px;background:#fff;border-radius:3px}

/* news */
.news{height:588px}
.news .section-title{position:absolute;left:112px;top:78px}
.news .lede{position:absolute;left:114px;top:144px;width:360px;color:#333}
.news .btn{left:112px;top:203px;width:111px;height:42px}
.news-lead{left:110px;top:265px;width:374px;height:234px;border-radius:5px;background:linear-gradient(120deg,#c9cdd2,#7d828a 55%,#b9bcc0)}
.news-card{position:absolute;top:89px;width:273px;height:402px;border-radius:5px;overflow:hidden}
.news-card .photo{inset:0}
.news-card p{position:absolute;left:35px;bottom:0;width:220px;height:146px;background:#fff;padding:44px 22px 0;font:600 16px/31px var(--head)}

/* accelerator */
.accelerator{height:458px;background:var(--blue)}
.accelerator h2{position:absolute;top:50px;width:1200px;text-align:center;color:#fff;font:700 44px var(--head)}
.pillar{position:absolute;top:143px;width:318px;height:251px;background:#fff;border-radius:6px}
.pillar .badge{position:absolute;left:24px;top:19px;width:82px;height:82px;border-radius:50%;background:var(--yellow);display:flex;align-items:center;justify-content:center}
.pillar h3{position:absolute;left:117px;top:60px;font:400 25px var(--head)}
.pillar p{position:absolute;left:30px;top:118px;width:265px;font:400 12px/28px var(--body);color:var(--grey)}

/* testimonials */
.testimonials{height:456px}
.testimonials .section-title{position:absolute;left:117px;top:78px}
.testimonials .btn{left:975px;top:87px;width:110px;height:42px}
.quote{position:absolute;top:152px;width:318px;height:217px;background:#fff;border-radius:5px;box-shadow:0 2px 8px rgba(0,0,0,.18)}
.avatar{position:absolute;left:22px;top:22px;width:46px;height:46px;border-radius:50%;background:linear-gradient(160deg,#c8c4c0,#6c6660)}
.quote h4{position:absolute;left:80px;top:26px;font:500 17px var(--head);white-space:nowrap}
.quote .role{position:absolute;left:80px;top:52px;font:400 14px var(--head);color:var(--blue)}
.stars{position:absolute;right:18px;top:24px;color:var(--yellow);font-size:15px;letter-spacing:0}
.quote p{position:absolute;left:26px;top:98px;width:270px;font:400 12px/24px var(--body);color:var(--grey)}
.quote a{position:absolute;left:26px;top:178px;font:400 12px var(--body);color:var(--blue)}
.quote .mark{position:absolute;right:22px;top:174px;color:var(--blue);font:800 28px/1 var(--head)}

/* footer */
.site-footer{height:381px;background:var(--footer-bg)}
.site-footer .brand{left:112px;top:64px}
.subscribe-field{position:absolute;left:112px;top:156px;width:302px;height:53px;background:#fff;border-radius:4px;padding:17px 24px;font:500 14px var(--head)}
.site-footer .btn{left:112px;top:222px;width:109px;height:42px}
.socials{position:absolute;left:112px;top:290px;display:flex;gap:8px}
.socials i{display:block;width:28px;height:28px;border-radius:50%;background:#aab0ba}
.socials i:first-child{background:var(--blue)}
.footer-col{position:absolute;top:74px}
.footer-col h5{font:500 21px var(--head);margin-bottom:14px}
.footer-col li{list-style:none;font:400 15px/31px var(--head)}
.contact-row{display:flex;align-items:center;gap:12px;font:400 15px var(--head);margin-bottom:21px}
.contact-row b{width:28px;height:28px;border-radius:50%;background:var(--blue);display:flex;align-items:center;justify-content:center}
.footer-rule{position:absolute;left:112px;top:337px;width:976px;height:1px;background:#666}
.copyright{position:absolute;top:352px;width:1200px;text-align:center;font:400 14px var(--head)}
</style>
</head>
<body>

<header class="site-header">
  <div class="brand">
    <span class="brand-mark"></span>
    <span class="brand-name">HARBORLIGHT<small>CHAMBER OF COMMERCE</small></span>
  </div>
  <nav class="nav">
    <a class="current" href="#">Home</a>
    <a href="#" style="left:540px">Resources</a>
    <a href="#" style="left:632px">Membership</a>
    <a href="#" style="left:732px">Programs</a>
    <a href="#" style="left:816px">Events</a>
    <a href="#" style="left:885px">Portocall</a>
  </nav>
  <a class="btn" href="#">Contact Us</a>
</header>

<section class="hero">
  <div class="photo hero-photo" role="img" aria-label="Southern California city skyline above a palm-lined lake"></div>
  <div class="hero-shade"></div>
  <h1>Connecting SoCal's Best and<br>Brightest Businesses!</h1>
  <a class="btn" href="#">Get Started</a>
</section>

<section class="services">
  <div class="services-title">
    <h2 class="section-title">Empowering <span class="accent">Businesses at Every Stage</span></h2>
  </div>
  <p class="lede">Lorem ipsum dolor sit amet, consectetur adipiscing elit, sed do eiusmod tempor incididunt ut labore et dolore magna aliqua. Ut enim ad minim veniam, quis nostrud exercitation ullamco laboris nisi ut aliquip ex ea commodo consequat.</p>
  <div class="service-card" style="left:110px;width:317px">
    <div class="photo" role="img" aria-label="Business team meeting around a table" style="background:linear-gradient(180deg,#cfc6bb 0%,#8d7f70 45%,#3b332c 100%)"></div>
    <p>Procurement and Contract<br>Assistance</p>
  </div>
  <div class="service-card featured" style="left:439px;width:318px">
    <div class="ring" role="img" aria-label="Colleagues working together at a laptop"></div>
    <p>Business Operations and<br>Managements</p>
  </div>
  <div class="service-card" style="left:769px;width:317px">
    <div class="photo" role="img" aria-label="Presenter at a whiteboard in an office" style="background:linear-gradient(180deg,#e4e6e8 0%,#a2a5a9 45%,#3a3d42 100%)"></div>
    <p>Marketing and Sales</p>
  </div>
  <a class="btn" href="#">View All</a>
</section>

<section class="impact">
  <div class="photo impact-photo" role="img" aria-label="Team collaborating around a desk with laptops"></div>
  <h2 class="section-title">Our <span class="accent">Impact</span></h2>
  <div class="stat" style="top:199px">
    <svg width="44" height="36" viewBox="0 0 44 36"><rect x="14" y="2" width="16" height="8" rx="2" fill="none" stroke="#1a66f5" stroke-width="4"/><rect x="2" y="9" width="40" height="25" rx="3" fill="#1a66f5"/><rect x="2" y="19" width="40" height="3" fill="#dde8fb"/></svg>
    <strong>4,000+</strong><span>Small Business Served</span>
  </div>
  <div class="stat" style="top:365px">
    <svg width="44" height="50" viewBox="0 0 44 50" style="top:38px"><path d="M14 4h16l-5 9h-6z" fill="#1a66f5"/><path d="M18 14h8c12 6 16 18 14 26-2 7-8 9-18 9S6 47 4 40C2 32 6 20 18 14z" fill="#1a66f5"/><text x="22" y="39" text-anchor="middle" fill="#fff" font-size="18" font-family="Arial" font-weight="700">$</text></svg>
    <strong>$43.1 Millions</strong><span style="left:136px;top:80px">received by Our businesses</span>
  </div>
  <div class="stat" style="top:533px">
    <svg width="54" height="50" viewBox="0 0 54 50" style="top:40px"><circle cx="27" cy="12" r="7" fill="#1a66f5"/><path d="M15 30c0-8 5-11 12-11s12 3 12 11z" fill="#1a66f5"/><path d="M4 36c8-4 16-2 22 2h10c6-4 12-4 16-2v6c-6-1-12 2-18 6H18L4 44z" fill="#1a66f5"/></svg>
    <strong>4,379+</strong><span>Jobs Retained</span>
  </div>
  <p class="impact-pitch">We build a healthy California economy by helping small business owners like you.</p>
  <p class="impact-copy">Duis aute irure dolor in reprehenderit in voluptate velit esse cillum dolore eu fugiat nulla pariatur. Excepteur sint occaecat cupidatat non proident, sunt in culpa qui officia deserunt mollit anim id est laborum.</p>
</section>

<section class="investors">
  <h2>Our Investers</h2>
  <div class="investor" style="left:42px"><i></i>Corvane Bank</div>
  <div class="investor" style="left:278px"><i></i>Miraleth</div>
  <div class="investor" style="left:468px"><i></i>Ostrand Supply</div>
  <div class="investor" style="left:680px">Quillmark</div>
  <div class="investor" style="left:793px"><i></i>Sennet Bank</div>
  <div class="investor" style="left:1010px"><i></i>Halvern Trust</div>
</section>

<section class="news">
  <h2 class="section-title">Latest <span class="accent">News</span></h2>
  <p class="lede">Sed ut perspiciatis unde omnis iste natus error sit eaque ipsa quae ab illo inventore veritatis et quas.</p>
  <a class="btn" href="#">View All</a>
  <div class="photo news-lead" role="img" aria-label="Colleagues discussing work at a laptop in a bright office"></div>
  <article class="news-card" style="left:523px">
    <div class="photo" role="img" aria-label="Smiling professional standing in an office with plants" style="background:linear-gradient(180deg,#d9dcd6,#9aa192 50%,#5d6357)"></div>
    <p>The standard Lorem Ipsum passage, used since the 1500s</p>
  </article>
  <article class="news-card" style="left:815px">
    <div class="photo" role="img" aria-label="Speaker presenting charts on a screen to a team" style="background:linear-gradient(180deg,#c8cdd3,#7c848e 50%,#3b4048)"></div>
    <p>Section 1.10.32 of "de Finibus Bonorum et Malorum</p>
  </article>
</section>

<section class="accelerator">
  <h2>Your Business Accelerator</h2>
  <div class="pillar" style="left:112px">
    <div class="badge"><svg width="40" height="34" viewBox="0 0 40 34"><rect x="4" y="20" width="32" height="8" rx="2" fill="#222"/><circle cx="10" cy="12" r="4" fill="#222"/><circle cx="20" cy="10" r="4" fill="#222"/><circle cx="30" cy="12" r="4" fill="#222"/><rect x="8" y="28" width="3" height="5" fill="#222"/><rect x="29" y="28" width="3" height="5" fill="#222"/></svg></div>
    <h3>Convene</h3>
    <p>Nemo enim ipsam voluptatem quia voluptas sit aspernatur aut odit aut fugit, sed quia consequuntur magni dolores eos qui ratione voluptatem sequi nesciunt.</p>
  </div>
  <div class="pillar" style="left:441px">
    <div class="badge"><svg width="30" height="40" viewBox="0 0 30 40"><path d="M15 1C7 1 2 7 2 14c0 10 13 25 13 25s13-15 13-25C28 7 23 1 15 1z" fill="#222"/><circle cx="15" cy="14" r="5" fill="#fec41a"/></svg></div>
    <h3>Navigate</h3>
    <p>Nemo enim ipsam voluptatem quia voluptas sit aspernatur aut odit aut fugit, sed quia consequuntur magni dolores eos qui ratione voluptatem sequi nesciunt.</p>
  </div>
  <div class="pillar" style="left:768px">
    <div class="badge"><svg width="36" height="40" viewBox="0 0 36 40"><circle cx="18" cy="10" r="8" fill="#222"/><path d="M3 39c0-12 6-18 15-18s15 6 15 18z" fill="#222"/><path d="M18 22l-3 5 3 10 3-10z" fill="#fec41a"/></svg></div>
    <h3>Advocate</h3>
    <p>Nemo enim ipsam voluptatem quia voluptas sit aspernatur aut odit aut fugit, sed quia consequuntur magni dolores eos qui ratione voluptatem sequi nesciunt.</p>
  </div>
</section>

<section class="testimonials">
  <h2 class="section-title">Client <span class="accent">Testimonials</span></h2>
  <a class="btn" href="#">View All</a>
  <div class="quote" style="left:112px">
    <div class="avatar" role="img" aria-label="Client portrait"></div>
    <h4>Rory Vant</h4><span class="role">Client</span><span class="stars">★★★★★</span>
    <p>Lorem ipsum dolor sit amet, consectetur adipiscing elit, sed do eiusmod tempor incididunt ut labore et dolore magna aliqua.</p>
    <a href="#">Read More...</a><span class="mark">&rdquo;</span>
  </div>
  <div class="quote" style="left:439px">
    <div class="avatar" role="img" aria-label="Client portrait"></div>
    <h4>Maris Delacourt</h4><span class="role">Client</span><span class="stars">★★★★★</span>
    <p>Lorem ipsum dolor sit amet, consectetur adipiscing elit, sed do eiusmod tempor incididunt ut labore et dolore magna aliqua.</p>
    <a href="#">Read More...</a><span class="mark">&rdquo;</span>
  </div>
  <div class="quote" style="left:766px">
    <div class="avatar" role="img" aria-label="Client portrait"></div>
    <h4>Tobin</h4><span class="role">Client</span><span class="stars">★★★★★</span>
    <p>Lorem ipsum dolor sit amet, consectetur adipiscing elit, sed do eiusmod tempor incididunt ut labore et dolore magna aliqua.</p>
    <a href="#">Read More...</a><span class="mark">&rdquo;</span>
  </div>
</section>

<footer class="site-footer">
  <div class="brand">
    <span class="brand-mark"></span>
    <span class="brand-name">HARBORLIGHT<small>CHAMBER OF COMMERCE</small></span>
  </div>
  <div class="subscribe-field">Enter Email Address</div>
  <a class="btn" href="#">Subscribe</a>
  <div class="socials"><i></i><i></i><i></i><i></i></div>
  <div class="footer-col" style="left:493px">
    <h5>Quick Links</h5>
    <ul><li>Home</li><li>Resources</li><li>Membership</li><li>Programs</li><li>Events</li><li>Portocall</li><li>Contact Us</li></ul>
  </div>
  <div class="footer-col" style="left:669px">
    <h5>Other Links</h5>
    <ul><li>Privacy Policy</li><li>Terms &amp; Conditions</li><li>Disclaimer</li><li>FAQ's</li><li>Support</li><li>Help</li></ul>
  </div>
  <div class="footer-col" style="left:856px">
    <h5 style="margin-bottom:18px">Contact Info</h5>
    <div class="contact-row"><b><svg width="12" height="16" viewBox="0 0 12 16"><path d="M6 0C3 0 0 2.5 0 6c0 4 6 10 6 10s6-6 6-10c0-3.5-3-6-6-6z" fill="#fff"/><circle cx="6" cy="6" r="2" fill="#1a66f5"/></svg></b>Lorem Ipsum,USA -437916</div>
    <div class="contact-row"><b><svg width="14" height="14" viewBox="0 0 14 14"><path d="M3 1l3 3-2 2c1 2 2 3 4 4l2-2 3 3-2 2C6 13 1 8 1 3z" fill="#fff"/></svg></b>+1 555 014 2290</div>
    <div class="contact-row"><b><svg width="14" height="10" viewBox="0 0 14 10"><rect width="14" height="10" rx="1" fill="#fff"/><path d="M1 1l6 5 6-5" fill="none" stroke="#1a66f5" stroke-width="1.4"/></svg></b>info@harborlightchamber.org</div>
  </div>
  <div class="footer-rule"></div>
  <p class="copyright">© 2025 &nbsp;Harborlight Chamber of Commerce.All rights reserved.</p>
</footer>

</body>
</html>
```